Marlow Sail Works President Business Card Carbon fiber catamarans

Hi.. I need a new business card design.. I am the President of a high tech yacht builder. We build Carbon Fiber go fast catamarans... Maybe we use the file I am sharing to you as the back of the card.. We need to look cool and crisp ...

Target Market(s)

Affluent People who will purchase a cool yacht

Industry/Entity Type

Custom Yacht Builder

Contact Information for Business Card

Dean Pellway , President, 731.508.2164 USA

Font styles to use
Serif

Requirements
Must have
• the clean crisp cool feel
Nice to have
• clean and crisp
Should not have
• Bold ugly

```html
<!DOCTYPE html>
<html lang="en">
<head>
<meta charset="utf-8">
<title>Marlow Sail Works – Business Card</title>
<link href="https://fonts.googleapis.com/css2?family=Arimo:wght@400;700&display=swap" rel="stylesheet">
<style>
  :root {
    --backdrop: #161617;
    --card: #2a2a2c;
    --card-edge: #8d8d90;
    --silver: #d9d9dc;
    --silver-soft: #b8b8bc;
    --emboss: #3b3b3e;
  }
  * { box-sizing: border-box; margin: 0; padding: 0; }
  html, body { width: 1200px; height: 963px; overflow: hidden; }
  body {
    background: var(--backdrop);
    font-family: "Arimo", Arial, sans-serif;
    position: relative;
  }
  .card {
    position: absolute;
    top: 333px;
    width: 520px;
    height: 297px;
    background: var(--card);
    border-radius: 18px;
    box-shadow: inset 0 0 0 1px var(--card-edge), 0 14px 30px rgba(0,0,0,.55);
    overflow: hidden;
  }
  .card--front { left: 50px; }
  .card--back { left: 630px; }

  .brand {
    position: absolute;
    display: flex;
    align-items: center;
    gap: 12px;
    font-weight: 700;
    letter-spacing: .18em;
    text-transform: uppercase;
  }
  .brand__dot { border-radius: 50%; flex: none; }
  .card--front .brand { left: 40px; top: 36px; font-size: 19px; color: var(--silver); }
  .card--front .brand__dot { width: 30px; height: 30px; background: var(--silver); }
  .card--back .brand { left: 50%; top: 50%; transform: translate(-50%,-50%); font-size: 24px; color: var(--emboss); white-space: nowrap; }
  .card--back .brand__dot { width: 40px; height: 40px; background: var(--emboss); }

  .accent-tab {
    position: absolute; left: 0; top: 104px;
    width: 4px; height: 34px;
    background: linear-gradient(var(--silver), #6d6d70);
  }
  .person { position: absolute; left: 30px; top: 108px; }
  .person__name { font-weight: 700; font-size: 17px; color: var(--silver); letter-spacing: .03em; text-transform: uppercase; }
  .person__role { font-size: 13px; color: var(--silver-soft); margin-top: 3px; }

  .contact { position: absolute; left: 30px; top: 176px; list-style: none; }
  .contact li {
    display: flex; align-items: center; gap: 9px;
    font-size: 13.5px; color: var(--silver); margin-bottom: 7px;
  }
  .contact svg { width: 13px; height: 13px; flex: none; }

  .address {
    position: absolute; right: 28px; bottom: 24px;
    text-align: right; font-size: 13px; line-height: 1.35; color: var(--silver);
  }
</style>
</head>
<body>
  <section class="card card--front" aria-label="Card front">
    <div class="brand"><span class="brand__dot"></span>Marlow Sail Works</div>
    <span class="accent-tab"></span>
    <div class="person">
      <p class="person__name">Dean Pellway</p>
      <p class="person__role">President</p>
    </div>
    <ul class="contact">
      <li>
        <svg viewBox="0 0 16 16" aria-hidden="true"><circle cx="8" cy="8" r="7.5" fill="#d9d9dc"/><path d="M5.3 4.2l1.4-.3.8 2-1 .8a5 5 0 0 0 2.8 2.8l.8-1 2 .8-.3 1.4c-3.6.4-7-3-6.5-6.5z" fill="#2a2a2c"/></svg>
        731.508.2164
      </li>
      <li>
        <svg viewBox="0 0 16 16" aria-hidden="true"><rect x="1" y="3.5" width="14" height="9" rx="1" fill="#d9d9dc"/><path d="M1.5 4l6.5 5 6.5-5" fill="none" stroke="#2a2a2c" stroke-width="1.2"/></svg>
        youremail@marlowmail.com
      </li>
      <li>
        <svg viewBox="0 0 16 16" aria-hidden="true"><circle cx="8" cy="8" r="7.5" fill="#d9d9dc"/><g fill="none" stroke="#2a2a2c" stroke-width="1"><circle cx="8" cy="8" r="5"/><ellipse cx="8" cy="8" rx="2.2" ry="5"/><path d="M3 8h10"/></g></svg>
        www.yourwebsite.com
      </li>
    </ul>
    <p class="address">Your address<br>city, state, ZIP 0000</p>
  </section>

  <section class="card card--back" aria-label="Card back">
    <div class="brand"><span class="brand__dot"></span>Marlow Sail Works</div>
  </section>
</body>
</html>
```